Cleaning Service Company In need of Good Web presence.

The company is a cleaning service company which provides professional staff and service for cleaning. This is a project to build a site that is both solid and a strong recognition of our organization. It is supposed to show quality, cleanliness, professionalism. The use of images and art for imagery is all good just to have a site that is consistent and solid. There might be a chance to make stationary, logo and business cars if someone feels they can build a brand that is consistent. The image we are going for is clean solid and to stand out. Finally stationary should not be expensive to print.

Current logo is attached and can be used or can be made more creative.

Target Market(s)

Corporate and Government entities, that will feel that this company has a brand that sets it apart from the rest. The company is new so the modification of the logo will not be an issue if a more solid brand come out of this project. The idea is to have a clean consistent product that stands our from others in terms of website, stationary, etc

Industry/Entity Type

Cleaning Service

Contact Information for Business Card

P.O.Box 51947
Riffa
Kingdom of Bahrain

Logo Text

Harbor Lane Services

Number of Pages Required

4 page

Font styles to use
Sans Serif

Colors
abd036
cadf82
eaf2ce
9bcb3b

Requirements
Must have
• Green Color to be used in order to stick to the name. Also the creativity and boldness in an elegant manner.
Nice to have
• Arabic name of company
• هاربر لين سرفسس ذ.م.م
• if cannot be put at least make a location should be chosen
• Also could be a bit of 3D given to the logo if it could stay elegent.
Should not have
• Should not show people cleaning.

```html
<!DOCTYPE html>
<html lang="en">
<head>
<meta charset="utf-8">
<title>Harbor Lane Services W.L.L</title>
<link href="https://fonts.googleapis.com/css2?family=Open+Sans:wght@400;600;700&family=Roboto:wght@400;500&family=Noto+Naskh+Arabic:wght@400&display=swap" rel="stylesheet">
<style>
:root{
  --green:#abd036;
  --green-bright:#9bcb3b;
  --green-soft:#cadf82;
  --green-pale:#eaf2ce;
  --forest:#1b7a4b;
  --forest-dark:#136a3f;
  --ink:#1f1f1f;
  --text:#555;
  --muted:#777;
  --grey-band:#f3f3f3;
  --line:#e2e2e2;
  --white:#fff;
}
*{margin:0;padding:0;box-sizing:border-box}
h1,h2,h3,h4{font-weight:400}
html,body{width:1200px;height:2423px;overflow:hidden;background:var(--white)}
body{position:relative;font-family:"Open Sans",sans-serif;color:var(--ink)}
.abs{position:absolute}

/* header */
.top-rule{left:0;top:0;width:1200px;height:4px;background:var(--forest)}
.brand{left:48px;top:40px;display:flex;align-items:center;gap:12px}
.brand-dot{width:48px;height:48px;border-radius:50%;background:var(--green)}
.brand-name{font-family:"Roboto",sans-serif;font-weight:500;font-size:18px;color:var(--forest);white-space:nowrap}
.phone{left:829px;top:23px;display:flex;align-items:center;gap:10px;font-family:"Roboto",sans-serif;font-size:21px;color:var(--ink)}
.phone-icon{width:20px;height:20px}
.social-top{left:1005px;top:26px;display:flex;gap:7px}
.social-top span{width:20px;height:20px;background:var(--forest);display:block}
.nav{left:0;top:74px;width:1200px;height:30px;font-family:"Roboto",sans-serif;font-size:15.5px;color:var(--ink)}
.nav a{position:absolute;top:0;height:30px;line-height:30px;text-decoration:none;color:inherit;white-space:nowrap}
.nav .active{background:var(--green);color:var(--white);border-radius:15px;width:91px;text-align:center}

/* hero */
.hero{left:0;top:126px;width:1200px;height:512px;background:linear-gradient(100deg,#6f6a55 0%,#3f4a2f 35%,#5a3f33 60%,#3a2a25 100%)}
.hero-title{left:0;top:322px;width:1200px;text-align:center;font-family:"Noto Naskh Arabic",serif;font-size:62px;line-height:90px;color:var(--white);direction:rtl}
.slider-arrow{width:26px;height:26px;border-radius:50%;background:rgba(20,20,20,.75)}

/* welcome */
.welcome-title{left:102px;top:730px;font-family:"Roboto",sans-serif;font-size:25px;color:var(--ink);white-space:nowrap}
.welcome-text{left:100px;top:772px;width:524px;font-size:11.5px;line-height:22.6px;color:var(--text)}
.btn-pill{background:var(--green);color:var(--white);border-radius:15px;text-align:center;font-size:14px}
.welcome-btn{left:100px;top:943px;width:115px;height:30px;line-height:30px}
.welcome-photo{left:638px;top:694px;width:517px;height:320px;background:linear-gradient(90deg,#f4f7f8,#e7eef0 45%,#f5f6f4)}

/* services */
.services{left:0;top:1011px;width:1200px;height:491px;background:var(--grey-band)}
.section-title{font-family:"Roboto",sans-serif;font-size:27px;color:var(--ink)}
.services-title{left:0;top:1062px;width:1200px;text-align:center}
.service-card{top:1135px;width:299px;height:286px;background:var(--white);box-shadow:0 1px 4px rgba(0,0,0,.18)}
.service-photo{width:299px;height:176px}
.service-name{margin-top:20px;text-align:center;font-family:"Roboto",sans-serif;font-size:16px;color:var(--ink)}
.service-desc{margin:4px auto 0;width:260px;text-align:center;font-size:12.4px;line-height:19px;color:var(--muted)}

/* blog */
.blog-title{left:95px;top:1598px;font-size:25px}
.blog-arrows{left:1088px;top:1598px;width:24px;height:18px}
.post-photo{top:1660px;width:162px;height:134px}
.post-body{top:1662px;width:312px}
.post-title{font-family:"Roboto",sans-serif;font-size:14px;color:var(--ink)}
.post-date{margin-top:9px;font-family:"Roboto",sans-serif;font-size:13px;color:var(--ink)}
.post-text{margin-top:8px;font-size:10.6px;line-height:19.2px;color:var(--text)}
.post-more{margin-top:6px;font-size:12px;color:var(--forest)}

/* call to action */
.cta{left:0;top:1894px;width:1200px;height:214px;background:linear-gradient(120deg,var(--forest) 0%,#1d8050 50%,var(--forest-dark) 100%)}
.cta-title{left:90px;top:1955px;font-size:25px;font-weight:600;color:var(--white)}
.cta-text{left:90px;top:1992px;width:700px;font-size:16.2px;line-height:26px;color:var(--white)}
.cta-btn{left:919px;top:1980px;width:194px;height:42px;line-height:42px;border-radius:21px;background:var(--white);color:var(--ink);text-align:center;font-family:"Roboto",sans-serif;font-size:18px}

/* footer */
.footer-brand{left:90px;top:2200px;width:210px}
.footer-brand .brand-dot{width:60px;height:60px;margin-bottom:12px}
.footer-brand .brand-name{font-size:17px;white-space:normal;line-height:22px}
.footer-head{top:2191px;font-family:"Roboto",sans-serif;font-size:15px;color:var(--ink)}
.footer-lines{top:2226px;font-size:11.8px;line-height:22px;color:var(--text)}
.mail-note{left:638px;top:2228px;width:200px;font-size:11.3px;line-height:17px;color:var(--text)}
.mail-form{left:638px;top:2269px;display:flex;height:29px}
.mail-input{width:149px;border:1px solid #cfcfcf;border-right:none;font-size:12px;color:var(--muted);padding:6px 7px}
.mail-submit{width:55px;background:var(--green);color:var(--white);font-size:12px;text-align:center;line-height:29px}
.social-foot{left:948px;top:2235px;display:flex;gap:14px}
.social-foot span{width:24px;height:24px;border-radius:4px;background:#5a5a5a;display:block}
.footer-rule{left:90px;top:2358px;width:1023px;height:1px;background:var(--line)}
.copyright{left:0;top:2380px;width:1200px;text-align:center;font-size:12px;color:var(--ink)}
</style>
</head>
<body>

<div class="abs top-rule"></div>

<header>
  <div class="abs brand">
    <span class="brand-dot"></span>
    <span class="brand-name">Harbor Lane Services</span>
  </div>

  <div class="abs phone">
    <svg class="phone-icon" viewBox="0 0 20 20" aria-hidden="true">
      <circle cx="10" cy="10" r="10" fill="#9bcb3b"/>
      <path d="M7 5.2c.4-.3.9-.2 1.1.2l.9 1.7c.2.4.1.8-.2 1.1l-.6.5c.5 1.1 1.4 2 2.5 2.6l.5-.6c.3-.3.7-.4 1.1-.2l1.7.9c.4.2.5.7.2 1.1l-.6.8c-.5.6-1.3.8-2 .5-2.5-1-4.4-2.9-5.4-5.4-.3-.7-.1-1.5.5-2z" fill="#fff"/>
    </svg>
    <span>312 640 2958</span>
  </div>

  <div class="abs social-top" aria-label="Social links"><span></span><span></span><span></span><span></span></div>

  <nav class="abs nav">
    <a class="active" style="left:326px">HOME</a>
    <a style="left:446px">ABOUT US</a>
    <a style="left:572px">SERVICES</a>
    <a style="left:691px">PROJECT</a>
    <a style="left:801px">SUPPORTS</a>
    <a style="left:929px">BLOG</a>
    <a style="left:1022px">CONTACT US</a>
  </nav>
</header>

<section>
  <div class="abs hero" role="img" aria-label="Hero photograph: exterior pressure washing of a wooden wall among trees"></div>
  <h1 class="abs hero-title">هاربر لين سرفسس ذ.م.م</h1>
  <span class="abs slider-arrow" style="left:1048px;top:551px"></span>
  <span class="abs slider-arrow" style="left:1082px;top:551px"></span>
  <svg class="abs" style="left:1048px;top:551px" width="60" height="26" viewBox="0 0 60 26" aria-hidden="true">
    <path d="M15 8l-5 5 5 5" fill="none" stroke="#fff" stroke-width="2"/>
    <path d="M45 8l5 5-5 5" fill="none" stroke="#fff" stroke-width="2"/>
  </svg>
</section>

<section>
  <h2 class="abs welcome-title">WELCOME TO HARBOR LANE SERVICES W.L.L</h2>
  <p class="abs welcome-text">It is a long established fact that a reader will be distracted by the readable content of a page when looking at its layout. The point of using Lorem Ipsum is that it has a more-or-less normal distribution of letters, as opposed to using 'Content here, content here', making it look like readable English. Many desktop publishing packages and web page editors now use Lorem Ipsum as their default model text, and a search for 'lorem ipsum' will uncover many web sites still in their infancy. It has survived not only five centuries, but also the leap into electronic typesetting, remaining essentially unchanged. It was popularised</p>
  <div class="abs btn-pill welcome-btn">Read More</div>
  <div class="abs welcome-photo" role="img" aria-label="Photograph of two cleaning staff with buckets, brushes and dusters"></div>
</section>

<section>
  <div class="abs services"></div>
  <h2 class="abs section-title services-title">OUR SERVICES</h2>

  <article class="abs service-card" style="left:124px">
    <div class="service-photo" role="img" aria-label="Photograph of a polished floor being machine cleaned in an office lobby" style="background:linear-gradient(160deg,#8ea3b8,#c9d5de 55%,#e8edf0)"></div>
    <h3 class="service-name">GOVT AGENCIES CLEANING</h3>
    <p class="service-desc">It is a long established fact that a reader will be distracted by the readable content</p>
  </article>

  <article class="abs service-card" style="left:451px">
    <div class="service-photo" role="img" aria-label="Photograph of office dusting with a colourful feather duster" style="background:linear-gradient(150deg,#f1e8ea,#e9c9d6 50%,#f4f0ec)"></div>
    <h3 class="service-name">OFFICE CLEANING</h3>
    <p class="service-desc">It is a long established fact that a reader will be distracted by the readable content</p>
  </article>

  <article class="abs service-card" style="left:777px">
    <div class="service-photo" role="img" aria-label="Photograph of a bright living room being vacuumed" style="background:linear-gradient(150deg,#b9c3cb,#e6eaee 50%,#f7f7f5)"></div>
    <h3 class="service-name">HOME CLEANING</h3>
    <p class="service-desc">It is a long established fact that a reader will be distracted by the readable content</p>
  </article>
</section>

<section>
  <h2 class="abs section-title blog-title">LATEST BLOG</h2>
  <svg class="abs blog-arrows" viewBox="0 0 24 18" aria-hidden="true">
    <path d="M8 3l-6 6 6 6M16 3l6 6-6 6" fill="none" stroke="#222" stroke-width="2"/>
  </svg>

  <div class="abs post-photo" style="left:95px;background:linear-gradient(135deg,#dfe8ee,#b9d3e2 50%,#eef2f4)" role="img" aria-label="Blog photograph of cleaning staff holding supplies"></div>
  <article class="abs post-body" style="left:273px">
    <h3 class="post-title">Nemo Enim Ipsam Volup</h3>
    <p class="post-date">09-07-2017</p>
    <p class="post-text">Lorem Ipsum has been the industry's standard dummy text ever since the 1500s, when an unknown printer took a galley of type and scrambled it to make a type specimen book.</p>
    <p class="post-more">Read More &gt;&gt;</p>
  </article>

  <div class="abs post-photo" style="left:625px;background:linear-gradient(135deg,#eef1f2,#d9c6d3 50%,#f2f4f1)" role="img" aria-label="Blog photograph of a staff member with cleaning gloves and spray"></div>
  <article class="abs post-body" style="left:806px">
    <h3 class="post-title">Nemo Enim Ipsam Volup</h3>
    <p class="post-date">09-07-2017</p>
    <p class="post-text">Lorem Ipsum has been the industry's standard dummy text ever since the 1500s, when an unknown printer took a galley of type and scrambled it to make a type specimen book.</p>
    <p class="post-more">Read More &gt;&gt;</p>
  </article>
</section>

<section>
  <div class="abs cta"></div>
  <h2 class="abs cta-title">READY TO GET STARTED?</h2>
  <p class="abs cta-text">Lorem Ipsum has been the industry's standard dummy text ever since the 1500s, when an unknown printer took a galley of type and scrambled it to make a type specimen book.</p>
  <div class="abs cta-btn">GET STARTED</div>
</section>

<footer>
  <div class="abs footer-brand">
    <span class="brand-dot" style="display:block"></span>
    <span class="brand-name">Harbor Lane Services</span>
  </div>

  <h4 class="abs footer-head" style="left:326px">CONTACT US</h4>
  <p class="abs footer-lines" style="left:328px">Address : 14 Orchard Row, Eastgate<br>Dunmore, DM4 7QX<br>Phone : 07580 314 662<br>Email : hello@harborlane.example</p>

  <h4 class="abs footer-head" style="left:638px">JOIN OUR MAILING LIST</h4>
  <p class="abs mail-note">Your about us information would fit here nicely.</p>
  <div class="abs mail-form">
    <div class="mail-input">Email address</div>
    <div class="mail-submit">Submit</div>
  </div>

  <h4 class="abs footer-head" style="left:948px">FOLLOW US OUT THERE</h4>
  <div class="abs social-foot" aria-label="Social links"><span></span><span></span><span></span><span></span></div>

  <div class="abs footer-rule"></div>
  <p class="abs copyright">Copyright © 2017. All Rights Reserved</p>
</footer>

</body>
</html>
```